A4 Tri-fold Brochure for Sedation Dentist Specialist Dr. Marlon and Sedation Dentistry.

I would like to create an A4 tri-fold brochure for our Dental Sedation Specialist Dr. Marlon Duque. Please carefully select the most suitable highlights from his bio below.

This brochure has two parts. Highlighting what makes Dr. Marlon Duque unique and trustworthy. Include a picture of him (attached). The second part is about sedation dentistry. All you need to know here: http://www.calmchairhub.example/what-is-calm-chair-care

Avoid making it too wordy.

Meet Dr. Roel Benet Marlon Duque, DDS

Inspired to Become a Dentist:
As a child, Dr. Marlon Duque always felt stressed whenever he had to see a dentist. He knew that he wanted to become a dentist to help put patients completely at ease while they experienced quality dental care.

He is passionate about giving patients the healthy, beautiful smiles they deserve. “I find it fulfilling when I can see my patients’ beautiful smiles and how they can finally appreciate the joy of eating with a healthy set of teeth. However, what I love most about my job is the ability to provide a stress-free and comfortable experience at the dentist’s office, particularly for children, through sedation and general anesthesia.”

Educational Achievements:
Before becoming a dentist, Dr. Marlon Duque earned his undergraduate degree at the Northvale Institute of Arts where he received a Bachelor of Medical Science Honor Specialization degree with distinction in biochemistry. He then completed his Doctor of Dental Surgery degree with honors at the Kestrel Bay College. While there, he received the Linnet Orr Award in his class for outstanding achievement in anesthesia. He then pursued his three-year residency as well as a master’s degree in dental anesthesia at the Kestrel Bay College.

So he can provide his patients with the latest in dentistry, Dr. Marlon Duque enjoys pursuing additional knowledge, particularly in the areas of dental anesthesia as well as advanced technologies in dentistry. He is currently part of the Bright Arc study circle and has enrolled in the Core Anchor Short- Fellowship Course. He also serves as a clinical instructor at the Halvex Wing at the Kestrel Bay College.

Association Memberships:
In addition to his academic credentials, Dr. Marlon Duque is a member of several associations:
The Fenwick Board of Oral Practitioners of Ontario (FBOPO)
Dental Meridian Guild of Oral Sleep Care (MGOSC)
Northern Circle of Oral Calm Care (NCOCC)
Pellham Dental Alliance (PDA)
Outside the Practice

When he’s not at the practice, Dr. Marlon Duque enjoys spending time with his wife Dorla and their two poodles Pippa and Bramble, who are spoiled rotten! “Dorla and I love taking our dogs out on hikes and to the dog park on weekends. I also enjoy a wide range of activities from model building and playing the piano to soccer, gym and archery.” He stays fit by working out at the local Fitwell gym, and he likes to walk in Marrow Creek Park and Ashbury Field Park.

Dr. Marlon Duque considers himself to be a kid at heart. He is a big fan of superheroes and animated movies. “I get really excited about any upcoming superhero or Vellum Spark movies. Till this day, I still collect superhero toy figures.”

He supports the BrightWard Fund as well as the Lakeshore League for Animal Welfare and Rescue (LLAWR).

Experience outstanding dental care with our highly skilled dentist. Contact us today to schedule an appointment with Dr. Marlon Duque! He speaks English, Cantonese, and Mandarin.

Target Market(s)

Mothers with young kids.

Industry/Entity Type

Dental

Font styles to use
Sans Serif

Requirements
Should not have
• Prices

```html
<!DOCTYPE html>
<html lang="en">
<head>
<meta charset="utf-8">
<title>Dental Sedation Specialist – Tri-fold Brochure</title>
<link href="https://fonts.googleapis.com/css2?family=Rubik:wght@400;500;700&display=swap" rel="stylesheet">
<style>
:root{
  --page:#f1f1f1;
  --navy:#2d5899;
  --navy-deep:#1f3f78;
  --teal:#3db39a;
  --teal-soft:#47c2a6;
  --white:#ffffff;
  --ink-blue:#2a4f8f;
}
*{box-sizing:border-box;margin:0;padding:0}
h1,h2,h3{font-weight:400}
html,body{width:1200px;height:1200px;overflow:hidden;background:var(--page);font-family:'Rubik',Arial,sans-serif}
.spread{position:absolute;left:226px;width:748px;height:528px;overflow:hidden}
.spread--outside{top:46px;background:var(--white)}
.spread--inside{top:624px}
.abs{position:absolute}

/* outside spread */
.panel-about{left:0;top:0;width:250px;height:528px;background:var(--navy);color:var(--white)}
.panel-edge{left:674px;top:0;width:74px;height:528px;background:var(--navy)}
.about-icon{left:95px;top:20px}
.rule{height:1.5px;background:var(--teal)}
.about-title{left:0;width:250px;top:98px;text-align:center;color:var(--teal-soft);font-size:14px;font-weight:500}
.about-body{left:25px;top:124px;width:194px;font-size:8.4px;line-height:10.7px;text-align:justify}
.about-body p{margin-bottom:6.5px}
.about-body em{font-style:italic}
.cover-photo{left:386px;top:30px;width:343px;height:377px;background:linear-gradient(160deg,#7a5a45 0%,#a08474 35%,#c9c6c4 55%,#1d2b4a 80%,#1b2744 100%)}
.title-band{left:275px;top:290px;width:423px;height:81px;background:var(--teal)}
.title-shade{left:386px;top:290px;width:312px;height:81px;background:rgba(20,35,60,.55)}
.cover-title{left:511px;top:297px;width:212px;color:var(--white);font-weight:500;font-size:13.5px;line-height:17px;letter-spacing:.5px;text-transform:uppercase}
.contact-icon{left:275px;top:428px}
.contact-title{left:313px;top:437px;color:var(--ink-blue);font-size:12px;font-weight:500}
.contact-list{left:275px;top:462px;list-style:none;font-size:6.6px;color:var(--ink-blue)}
.contact-list li{display:flex;align-items:center;gap:8px;height:15px}
.inspired-icon{left:512px;top:426px}
.inspired-title{left:513px;top:464px;color:var(--ink-blue);font-size:14px;font-weight:500;line-height:17px}

/* inside spread */
.inside-bg{left:0;top:0;width:748px;height:528px;background:linear-gradient(135deg,#9fb8d8 0%,#4f79b3 30%,#2d5597 60%,#3c6aa8 85%,#1e3c6e 100%)}
.meet-box{left:26px;top:0;width:198px;height:50px;background:var(--navy);color:var(--white);font-size:12px;line-height:15px;text-align:center;padding-top:10px;font-weight:400}
.bio-panel{left:12px;top:69px;width:226px;height:459px;background:rgba(38,78,145,.82)}
.bio-frame{left:26px;top:82px;width:198px;height:446px;border:1.5px solid var(--white);border-bottom:none}
.bio-icon{left:38px;top:98px}
.bio-rule{left:91px;top:94px;width:46px}
.bio-heading{left:91px;top:101px;color:var(--teal-soft);font-size:8.8px;font-weight:400}
.bio-intro{left:91px;top:116px;width:126px;font-size:6.6px;line-height:8.6px;color:var(--white);text-align:justify}
.bio-quote{left:35px;top:178px;width:182px;font-size:6.6px;line-height:8.6px;color:var(--white);text-align:justify}
.bio-photo{left:22px;top:256px;width:216px;height:272px;background:linear-gradient(180deg,rgba(255,255,255,.15) 0%,#27365a 45%,#1c2844 100%)}
.main-panel{left:260px;top:12px;width:477px;height:500px;background:rgba(40,80,148,.82)}
.divider{left:498px;top:34px;width:6px;height:452px;background:var(--teal)}
.col{width:193px;color:var(--white);font-size:7px;line-height:9.5px;text-align:justify}
.col-edu{left:282px}
.col-life{left:523px}
.col-heading{width:193px;left:282px;text-align:center;color:var(--teal-soft);font-size:9px;font-weight:400}
.member-list{left:282px;top:422px;list-style:none;font-size:7px;line-height:9.6px;color:var(--white)}
</style>
</head>
<body>

<section class="spread spread--outside">
  <div class="abs panel-about">
    <svg class="abs about-icon" width="60" height="62" viewBox="0 0 60 62" fill="none" stroke="#3db39a" stroke-width="2" stroke-linecap="round" stroke-linejoin="round">
      <path d="M22 12c-6-3-16-1-16 10 0 8 4 12 6 22 1 6 3 12 6 12 4 0 3-12 8-12s4 12 8 12c3 0 5-6 6-12"/>
      <circle cx="42" cy="17" r="13"/>
      <path d="M42 10v14M35 17h14"/>
    </svg>
    <div class="abs rule" style="left:102px;top:88px;width:46px"></div>
    <h2 class="abs about-title">About oral sedation</h2>
    <div class="abs about-body">
      <p>Oral sedation dentistry allows appropriately trained dentists to create a safe and comfortable dental experience for patients who have avoided the dentist out of fear or who might have time restrictions.</p>
      <p>A dentist who has been trained to implement sedation can effectively helping a patient become as comfortable and relaxed as possible using well established and proven protocols with a variety of sedation medications administered orally and sublingually (under the tongue). These protocols can be customized for the patient’s individual emotional and physical needs.</p>
      <p>Sometimes referred to as ‘relaxation’, ‘sleep’ or ‘anxiety free’ dentistry, this comfortable care is now offered by thousands of trained dentists all over the US and Canada.</p>
      <p>“Oral conscious sedation has provided access to care for hundreds of thousands of Americans who otherwise would have been without the dental care they need. Dentists who have received comprehensive training from the Calm Care Training Council have an amazing tool to treat patients safely and comfortably, often correcting years of professional neglect in just a few visits. No longer does fear, or the inconvenience of having multiple visits, have to be the overwhelming obstacle that it has been in the past. When it comes to the impact on the dental health of the United States, conscious sedation dentistry stands as one of the most meaningful advances of the past century.” – <em>Harlan P Voss, DMD; Dean CSA Faculty</em></p>
    </div>
  </div>

  <div class="abs panel-edge"></div>
  <div class="abs cover-photo" role="img" aria-label="Portrait of the dentist in navy scrubs with a stethoscope, smiling in the clinic"></div>
  <div class="abs title-band"></div>
  <div class="abs title-shade"></div>
  <h1 class="abs cover-title">Dental Sedation Specialist Dr. Roel Benet Marlon Duque, DDS</h1>

  <svg class="abs contact-icon" width="34" height="30" viewBox="0 0 34 30" fill="none" stroke="#3db39a" stroke-width="1.6" stroke-linecap="round" stroke-linejoin="round">
    <path d="M4 10c0 8 8 16 16 17l3-4-4-3-2 2c-3-1-6-4-7-7l2-2-3-4z"/>
    <circle cx="23" cy="10" r="8"/>
    <path d="M19 9h8M23 5v8"/>
  </svg>
  <div class="abs contact-title">Contact us</div>
  <ul class="abs contact-list">
    <li><svg width="9" height="9" viewBox="0 0 10 10"><circle cx="5" cy="5" r="4" fill="none" stroke="#3db39a" stroke-width="1.4"/><path d="M1 5h8M5 1v8" stroke="#3db39a" stroke-width="1"/></svg>www.calmchairhub.example</li>
    <li><svg width="9" height="9" viewBox="0 0 10 10"><path d="M1 2c0 4 3 7 7 7l1-2-2-1-1 1C4 6 3 5 2 4l1-1-1-2z" fill="#3db39a"/></svg>0.987.654.32</li>
    <li><svg width="9" height="9" viewBox="0 0 10 10"><path d="M1 5l8-4-3 8-1-3z" fill="#3db39a"/></svg>hello@calmchairhub.example</li>
  </ul>

  <svg class="abs inspired-icon" width="40" height="32" viewBox="0 0 40 32" fill="none" stroke="#3db39a" stroke-width="1.6" stroke-linecap="round" stroke-linejoin="round">
    <path d="M14 6c3-2 5 0 6 0s3-2 6 0c3 3 0 8-1 14-1 5-2 8-3 8s-1-6-2-6-1 6-2 6-2-3-3-8c-1-6-4-11-1-14z"/>
    <path d="M4 10h5M4 18l4-2M31 10h5M32 16l4 2M11 3l2 2M29 3l-2 2M20 1v3"/>
  </svg>
  <h2 class="abs inspired-title">Inspired to<br>Become a Dentist</h2>
</section>

<section class="spread spread--inside">
  <div class="abs inside-bg" role="img" aria-label="Soft-focus dental clinic scene with instruments in blue tones"></div>

  <div class="abs meet-box">Meet Dr. Roel Benet<br>Marlon Duque, DDS</div>
  <div class="abs bio-panel"></div>
  <div class="abs bio-frame"></div>
  <svg class="abs bio-icon" width="48" height="52" viewBox="0 0 48 52" fill="none" stroke="#3db39a" stroke-width="1.6" stroke-linecap="round">
    <path d="M10 44V34c-4-3-6-8-6-13C4 11 12 4 22 4s18 7 18 16l4 8h-4v8h-8v8"/>
    <circle cx="20" cy="34" r="5"/><circle cx="20" cy="34" r="2"/>
    <path d="M8 6l2 2M20 0v3M32 6l-2 2"/>
  </svg>
  <div class="abs rule bio-rule"></div>
  <h3 class="abs bio-heading">Inspired to Become a Dentist</h3>
  <p class="abs bio-intro">As a child, Dr. Marlon Duque always felt stressed whenever he had to see a dentist. He knew that he wanted to become a dentist to help put patients completely at ease while they experienced quality dental care.</p>
  <p class="abs bio-quote">He is passionate about giving patients the healthy, beautiful smiles they deserve. “I find it fulfilling when I can see my patients’ beautiful smiles and how they can finally appreciate the joy of eating with a healthy set of teeth. However, what I love most about my job is the ability to provide a stress-free and comfortable experience at the dentist’s office, particularly for children, through sedation and general anesthesia.”</p>
  <div class="abs bio-photo" role="img" aria-label="Portrait of the dentist in navy scrubs leaning on a counter"></div>

  <div class="abs main-panel"></div>
  <div class="abs divider"></div>

  <svg class="abs" style="left:350px;top:40px" width="56" height="52" viewBox="0 0 56 52" fill="none" stroke="#3db39a" stroke-width="1.6" stroke-linecap="round">
    <path d="M12 8c-8 8-8 24 4 34M44 8c8 8 8 24-4 34M16 42l12 6 12-6"/>
    <path d="M22 14c2-2 4 0 6 0s4-2 6 0c2 3 0 7-1 12-1 4-1 6-2 6s-1-5-3-5-2 5-3 5-1-2-2-6c-1-5-3-9-1-12z"/>
  </svg>
  <h3 class="abs col-heading" style="top:106px">Educational Achievements</h3>
  <p class="abs col col-edu" style="top:124px">Before becoming a dentist, Dr. Marlon Duque earned his undergraduate degree at the Northvale Institute of Arts where he received a Bachelor of Medical Science Honor Specialization degree with distinction in biochemistry. He then completed his Doctor of Dental Surgery degree with honors at the Kestrel Bay College. While there, he received the Linnet Orr Award in his class for outstanding achievement in anesthesia. He then pursued his three-year residency as well as a master’s degree in dental anesthesia at the Kestrel Bay College.</p>
  <p class="abs col col-edu" style="top:229px">So he can provide his patients with the latest in dentistry, Dr. Marlon Duque enjoys pursuing additional knowledge, particularly in the areas of dental anesthesia as well as advanced technologies in dentistry. He is currently part of the Bright Arc study circle and has enrolled in the Core Anchor Short- Fellowship Course. He also serves as a clinical instructor at the Halvex Wing at the Kestrel Bay College.</p>

  <svg class="abs" style="left:350px;top:322px" width="56" height="32" viewBox="0 0 56 32" fill="none" stroke="#3db39a" stroke-width="1.6" stroke-linejoin="round">
    <path d="M2 6l10-2 8 4 8-3 8 2 6 10-16 12-16-10-8-4z"/>
    <path d="M20 8l-6 6 4 2 8-5 12 11M42 17l12-3-4-10-10 2"/>
  </svg>
  <h3 class="abs col-heading" style="top:379px">Association Memberships</h3>
  <p class="abs col col-edu" style="top:396px">In addition to his academic credentials, Dr. Marlon Duque is a member of several associations:</p>
  <ul class="abs member-list">
    <li>The Fenwick Board of Oral Practitioners of Ontario (FBOPO)</li>
    <li>Dental Meridian Guild of Oral Sleep Care (MGOSC)</li>
    <li>Northern Circle of Oral Calm Care (NCOCC)</li>
    <li>Pellham Dental Alliance (PDA)</li>
    <li>Outside the Practice</li>
  </ul>

  <svg class="abs" style="left:590px;top:42px" width="60" height="46" viewBox="0 0 60 46" fill="none" stroke="#3db39a" stroke-width="1.6" stroke-linejoin="round">
    <path d="M4 44V20L30 4l26 16v24z"/><path d="M22 44V28h16v16"/>
  </svg>
  <p class="abs col col-life" style="top:96px">When he’s not at the practice, Dr. Marlon Duque enjoys spending time with his wife Dorla and their two poodles Pippa and Bramble, who are spoiled rotten! “Dorla and I love taking our dogs out on hikes and to the dog park on weekends. I also enjoy a wide range of activities from model building and playing the piano to soccer, gym and archery.” He stays fit by working out at the local Fitwell gym, and he likes to walk in Marrow Creek Park and Ashbury Field Park.</p>

  <svg class="abs" style="left:596px;top:192px" width="50" height="48" viewBox="0 0 50 48" fill="none" stroke="#3db39a" stroke-width="1.6" stroke-linejoin="round">
    <path d="M22 40L6 24C-2 14 10 2 18 10l4 4 4-4c6-6 14-2 14 4"/>
    <path d="M30 20c2-2 4 0 6 0s4-2 6 0c2 3 0 7-1 12-1 5-2 8-3 8s-1-6-2-6-1 6-2 6-2-3-3-8c-1-5-3-9-1-12z"/>
  </svg>
  <p class="abs col col-life" style="top:248px">Dr. Marlon Duque considers himself to be a kid at heart. He is a big fan of superheroes and animated movies. “I get really excited about any upcoming superhero or Vellum Spark movies. Till this day, I still collect superhero toy figures.”</p>

  <svg class="abs" style="left:594px;top:294px" width="52" height="48" viewBox="0 0 52 48" fill="none" stroke="#3db39a" stroke-width="1.6" stroke-linejoin="round">
    <path d="M18 6c3-2 5 0 8 0s5-2 8 0c3 4 0 9-1 15-1 5-2 8-3 8s-1-6-4-6-3 6-4 6-2-3-3-8c-1-6-4-11-1-15z"/>
    <path d="M4 20l4 14 10 10M48 20l-4 14-10 10M42 4l2 4 4 1-4 1-2 4-1-4-4-1 4-1z"/>
  </svg>
  <p class="abs col col-life" style="top:352px">He supports the BrightWard Fund as well as the Lakeshore League for Animal Welfare and Rescue (LLAWR).</p>

  <svg class="abs" style="left:596px;top:390px" width="50" height="44" viewBox="0 0 50 44" fill="none" stroke="#3db39a" stroke-width="1.6" stroke-linejoin="round">
    <path d="M18 4h22a8 8 0 018 8v8a8 8 0 01-8 8h-6l-6 6v-6h-2"/>
    <path d="M4 22c2-2 4 0 6 0s4-2 6 0c2 3 0 7-1 11-1 4-1 7-2 7s-1-5-3-5-2 5-3 5-1-3-2-7c-1-4-3-8-1-11z"/>
  </svg>
  <p class="abs col col-life" style="top:449px">Experience outstanding dental care with our highly skilled dentist. Contact us today to schedule an appointment with Dr. Marlon Duque! He speaks English, Cantonese, and Mandarin.</p>
</section>

</body>
</html>
```